Business card for Sports Apparel business

DOUBLE SIDED DESIGN
We need business cards for a new sports apparel business. We are developing a protective headband for soccer initially.
Torvalle is focused on designing and developing head protection products to reduce the likelihood of concussion when playing sports. Exploring and understanding medical insights, material science research, current and former players experiences and governing bodies guidelines has allowed Torvalle to develop the safety, style, form and function requirements of a suitable product to bring to market.
Target Market(s)
Mums buying kits for the sons and daughters. Amateur footballers.
Industry/Entity Type
Sporting Good
Contact Information for Business Card
Martin Ashworth - CEO
Mobile: +44 7431589027
Email: martin@torvalle.co.uk
Tel: 0208 5519372
Helena Pargeter - COO
Mob: +44 7385 640117
Email: helena@torvalle.co.uk
Tel: 0208 5519372
Duncan Farrow - CCO
Mob: +44 7564 293081
Email: duncan@torvalle.co.uk
Tel: 0208 5519372
Look and feel
Each slider illustrates characteristics of the customer's brand and the style your logo design should communicate.

```html
<!DOCTYPE html>
<html lang="en">
<head>
<meta charset="utf-8">
<title>Torvalle Business Card</title>
<link rel="stylesheet" href="https://fonts.googleapis.com/css2?family=Oswald:wght@600&family=Montserrat:wght@300;400;600&display=swap">
<style>
  :root {
    --backdrop: #d3d8da;
    --card-white: #f4f4f2;
    --brand-blue: #0f5a96;
    --ink-grey: #6d6f72;
    --shadow: rgba(40, 50, 60, 0.22);
  }
  * { margin: 0; padding: 0; box-sizing: border-box; }
  html, body {
    width: 1200px;
    height: 852px;
    overflow: hidden;
    background: var(--backdrop);
  }
  .canvas {
    position: relative;
    width: 1200px;
    height: 852px;
    display: flex;
    align-items: center;
    justify-content: center;
    gap: 60px;
  }
  .card {
    position: relative;
    width: 520px;
    height: 297px;
    border-radius: 3px;
    box-shadow: 0 14px 30px var(--shadow);
  }
  .card-front {
    background: var(--card-white);
  }
  .card-back {
    background: var(--brand-blue);
    display: flex;
    align-items: center;
    justify-content: center;
  }
  .identity {
    position: absolute;
    right: 278px;
    top: 112px;
    text-align: right;
  }
  .person-name {
    font-family: "Oswald", sans-serif;
    font-weight: 600;
    font-size: 27px;
    letter-spacing: 0.2px;
    line-height: 1.05;
    color: var(--brand-blue);
    text-transform: uppercase;
    white-space: nowrap;
  }
  .person-role {
    font-family: "Montserrat", sans-serif;
    font-weight: 400;
    font-size: 13px;
    color: var(--ink-grey);
    margin-top: 3px;
    letter-spacing: 0.5px;
  }
  .divider {
    position: absolute;
    left: 260px;
    top: 112px;
    width: 2px;
    height: 66px;
    background: var(--brand-blue);
  }
  .contact-list {
    position: absolute;
    left: 280px;
    top: 110px;
    list-style: none;
  }
  .contact-item {
    display: flex;
    align-items: center;
    gap: 9px;
    font-family: "Montserrat", sans-serif;
    font-weight: 300;
    font-size: 13.5px;
    color: var(--ink-grey);
    line-height: 22px;
    letter-spacing: 0.3px;
  }
  .contact-icon {
    width: 12px;
    height: 12px;
    flex: none;
  }
  .wordmark {
    font-family: "Montserrat", sans-serif;
    font-weight: 600;
    font-size: 52px;
    letter-spacing: 4px;
    color: #ffffff;
    text-transform: uppercase;
  }
</style>
</head>
<body>
  <main class="canvas">
    <section class="card card-front" aria-label="Card front">
      <div class="identity">
        <p class="person-name">Martin Ashworth</p>
        <p class="person-role">CEO</p>
      </div>
      <div class="divider"></div>
      <ul class="contact-list">
        <li class="contact-item">
          <svg class="contact-icon" viewBox="0 0 12 12" aria-hidden="true">
            <path d="M2.2 1 L4.2 1 L5 3.4 L3.8 4.4 C4.5 5.9 5.9 7.4 7.6 8.2 L8.6 7 L11 7.8 L11 9.8 C11 10.5 10.4 11 9.7 11 C5 10.6 1.4 7 1 2.3 C1 1.6 1.5 1 2.2 1 Z" fill="var(--brand-blue)"/>
          </svg>
          <span>0208 5519372</span>
        </li>
        <li class="contact-item">
          <svg class="contact-icon" viewBox="0 0 12 12" aria-hidden="true">
            <rect x="3" y="0.8" width="6" height="10.4" rx="1" fill="none" stroke="var(--brand-blue)" stroke-width="1.3"/>
            <circle cx="6" cy="9.3" r="0.7" fill="var(--brand-blue)"/>
          </svg>
          <span>+44 7431589027</span>
        </li>
        <li class="contact-item">
          <svg class="contact-icon" viewBox="0 0 12 12" aria-hidden="true">
            <rect x="0.8" y="2.3" width="10.4" height="7.4" rx="0.8" fill="none" stroke="var(--brand-blue)" stroke-width="1.3"/>
            <path d="M1 2.6 L6 6.5 L11 2.6" fill="none" stroke="var(--brand-blue)" stroke-width="1.3"/>
          </svg>
          <span>martin@torvalle.co.uk</span>
        </li>
      </ul>
    </section>

    <section class="card card-back" aria-label="Card back">
      <p class="wordmark">Torvalle</p>
    </section>
  </main>
</body>
</html>
```